Roofing company in Toronto, Canada needs a logo design and business card design

We need a business card and logo created for our company. Our company is "KLV Roofing" which provides roofing services for commercial and residential customers. We serve customers in the Greater Toronto Area (in Canada) thus the name KLV.

We want the logo and business card to be a modern design displaying professionalism and quality in the work. We would prefer rounded corners for the business cards but are open to other ideas. The cards should be pleasant and appealing to customers.

Target Market(s)

Commercial and Residential customers

Industry/Entity Type

Roofing

Contact Information for Business Card

Logo Text

KLV Roofing

Requirements
Nice to have
• Colours that are pleasing to the eye but at the same time should stand out from other business cards. If the design can incorporate the name of KLV Roofing and the actual concept of roofing that would be nice.
Should not have
• Do not want the business cards or logo to be childish looking. Need to look professionally designed.

```html
<!DOCTYPE html>
<html lang="en">
<head>
<meta charset="utf-8">
<title>KLV Roofing – Business Card</title>
<link href="https://fonts.googleapis.com/css2?family=Lato:wght@400;700;900&display=swap" rel="stylesheet">
<style>
  :root{
    --stage:#3a332f;
    --card-dark:#2b2b2b;
    --card-light:#ffffff;
    --brand-red:#e31e24;
    --ink:#231f20;
    --band-dark:#2e2e2e;
    --muted:#d9d9d9;
  }
  *{box-sizing:border-box;margin:0;padding:0}
  html,body{width:1200px;height:780px;overflow:hidden}
  body{background:var(--stage);font-family:'Lato',sans-serif;position:relative}
  .card{position:absolute;width:540px;height:309px;border-radius:6px;overflow:hidden;box-shadow:0 14px 30px rgba(0,0,0,.45)}
  .card--front{left:40px;top:120px;background:var(--card-dark)}
  .card--back{left:620px;top:350px;background:var(--card-light)}

  .wordmark{position:absolute;display:flex;align-items:center;gap:10px;font-weight:900;color:var(--brand-red);letter-spacing:1px;white-space:nowrap;line-height:1}
  .wordmark__square{display:block;background:var(--brand-red)}
  .card--front .wordmark{left:44px;top:76px;font-size:40px}
  .card--front .wordmark__square{width:22px;height:22px}
  .front__web{position:absolute;left:46px;top:132px;color:var(--muted);font-size:14px}

  .person{position:absolute;left:36px;top:34px;display:flex;align-items:center;gap:12px}
  .person__name{font-weight:900;font-size:20px;color:var(--ink);letter-spacing:.5px;line-height:1.2}
  .person__title{font-size:14px;color:var(--brand-red);line-height:1.2}
  .person__bar{display:block;width:7px;height:30px;background:var(--brand-red);flex:none}

  .contacts{position:absolute;left:34px;top:150px;list-style:none}
  .contacts li{display:flex;align-items:center;gap:8px;font-size:14px;color:var(--ink);height:18px}
  .contacts svg{width:13px;height:13px;flex:none}

  .card--back .wordmark{right:40px;top:134px;font-size:38px}
  .card--back .wordmark__square{width:20px;height:20px}
  .address{position:absolute;right:40px;top:184px;text-align:right;font-size:14px;color:var(--ink);line-height:1.3}

  .band{position:absolute;left:0;bottom:0;width:540px;height:80px}
</style>
</head>
<body>
  <section class="card card--front" aria-label="Business card front">
    <div class="wordmark"><span class="wordmark__square"></span>KLV Roofing</div>
    <p class="front__web">www.klvroofing.ca</p>
  </section>

  <section class="card card--back" aria-label="Business card back">
    <div class="person">
      <div class="person__text">
        <p class="person__name">DANIEL BROOKS</p>
        <p class="person__title">Managing Director</p>
      </div>
      <span class="person__bar"></span>
    </div>

    <ul class="contacts">
      <li><svg viewBox="0 0 13 13"><rect width="13" height="13" rx="2" fill="var(--brand-red)"/><path d="M4 3h2l.6 2-1 .8a5 5 0 0 0 1.6 1.6l.8-1 2 .6v2A1 1 0 0 1 9 10 6 6 0 0 1 3 4a1 1 0 0 1 1-1z" fill="#fff"/></svg>(01) 5550 1842</li>
      <li><svg viewBox="0 0 13 13"><rect width="13" height="13" rx="2" fill="var(--brand-red)"/><rect x="3" y="5" width="7" height="5" fill="#fff"/><rect x="4" y="3" width="5" height="2" fill="#fff"/></svg>(01) 5550 1843</li>
      <li><svg viewBox="0 0 13 13"><rect width="13" height="13" rx="2" fill="var(--brand-red)"/><rect x="3" y="4" width="7" height="5" fill="#fff"/><path d="M3 4l3.5 3L10 4" stroke="var(--brand-red)" fill="none"/></svg>info@klvroofing.ca</li>
      <li><svg viewBox="0 0 13 13"><rect width="13" height="13" rx="2" fill="var(--brand-red)"/><circle cx="6.5" cy="6.5" r="3.5" fill="none" stroke="#fff"/><path d="M3 6.5h7M6.5 3v7" stroke="#fff"/></svg>www.klvroofing.ca</li>
    </ul>

    <div class="wordmark"><span class="wordmark__square"></span>KLV Roofing</div>
    <p class="address">PO BOX 480 Harbour Lane<br>2nd street Toronto, Canada</p>

    <svg class="band" viewBox="0 0 540 80" preserveAspectRatio="none" aria-hidden="true">
      <path d="M0 6H370Q380 6 386 14L400 40Q405 48 415 48H540V52H413Q402 52 396 43L382 18Q377 10 368 10H0Z" fill="var(--band-dark)"/>
      <path d="M0 15H366Q374 15 379 23L392 48Q398 58 410 58H540V80H0Z" fill="var(--brand-red)"/>
    </svg>
  </section>
</body>
</html>
```